BRIGHT RIVER POWER.

I'd like my business logo.
contact name: Dennis Halvorsen
phone:0438759164
email: info@brightriverpower.net.au
website: www.brightriverpower.net.au

services:
solar
battery storage
LED lighting
energy saving solutions
general electrical
I'd like the design to look professional

Target Market(s)

Everyone

Industry/Entity Type

Business

Contact Information for Business Card

as described above

Requirements
Must have
• Id like the colours and the design to work well with my logo.

```html
<!DOCTYPE html>
<html lang="en">
<head>
<meta charset="utf-8">
<title>Bright River Power – Business Card</title>
<link href="https://fonts.googleapis.com/css2?family=Source+Sans+3:wght@400;600;700&display=swap" rel="stylesheet">
<style>
  :root {
    --backdrop: #e8e3da;
    --card: #ffffff;
    --green: #4aa53f;
    --green-deep: #3a8f35;
    --green-light: #6cbd4e;
    --orange: #f2a320;
    --ink: #3a3a3a;
    --white: #ffffff;
  }
  * { margin: 0; padding: 0; box-sizing: border-box; }
  html, body {
    width: 1200px; height: 843px; overflow: hidden;
    background: var(--backdrop);
    font-family: "Source Sans 3", "Myriad Pro", sans-serif;
  }
  .stage {
    position: relative; width: 1200px; height: 843px;
    display: flex; align-items: center; justify-content: center; gap: 50px;
  }
  .card {
    position: relative; width: 540px; height: 330px;
    background: var(--card); border-radius: 18px; overflow: hidden;
    box-shadow: 0 6px 18px rgba(0,0,0,0.15);
  }

  /* Back face */
  .card--back { display: flex; flex-direction: column; align-items: center; justify-content: center; }
  .brand-lockup { display: flex; align-items: center; gap: 14px; }
  .brand-dot { width: 34px; height: 34px; border-radius: 50%; background: var(--orange); }
  .brand-name { font-size: 36px; font-weight: 600; color: var(--green); letter-spacing: 0.5px; }
  .services {
    margin-top: 34px; text-align: center; font-size: 15px; color: var(--ink);
    line-height: 1.55; letter-spacing: 0.3px;
  }
  .services .sep { color: var(--green); margin: 0 5px; }

  /* Front face */
  .card--front .brand-name {
    position: absolute; left: 38px; top: 34px; font-size: 32px;
  }
  .card-art { position: absolute; inset: 0; }
  .holder-name {
    position: absolute; left: 40px; top: 178px;
    font-size: 21px; font-weight: 700; color: var(--green);
  }
  .contact {
    position: absolute; right: 30px; top: 198px;
    text-align: right; color: var(--white); font-size: 17px; line-height: 1.45;
    list-style: none;
  }
</style>
</head>
<body>
<main class="stage">
  <section class="card card--back" aria-label="Card back">
    <div class="brand-lockup">
      <span class="brand-dot"></span>
      <span class="brand-name">BRIGHT RIVER POWER</span>
    </div>
    <p class="services">
      Solar<span class="sep">•</span>Battery Storage<span class="sep">•</span>LED Lighting<br>
      Energy Saving Solutions<span class="sep">•</span>General Electrical
    </p>
  </section>

  <section class="card card--front" aria-label="Card front">
    <svg class="card-art" width="540" height="330" viewBox="0 0 540 330" aria-hidden="true">
      <defs>
        <linearGradient id="sunFill" x1="0" y1="0" x2="1" y2="1">
          <stop offset="0" stop-color="var(--green-light)"/>
          <stop offset="0.5" stop-color="var(--green)"/>
          <stop offset="1" stop-color="var(--green-deep)"/>
        </linearGradient>
      </defs>
      <circle cx="475" cy="390" r="262" fill="none" stroke="var(--orange)" stroke-width="3"/>
      <circle cx="475" cy="390" r="252" fill="url(#sunFill)"/>
    </svg>
    <span class="brand-name">BRIGHT RIVER POWER</span>
    <p class="holder-name">Dennis Halvorsen</p>
    <ul class="contact">
      <li>Phone: 0438759164</li>
      <li>info@brightriverpower.net.au</li>
      <li>www.brightriverpower.net.au</li>
    </ul>
  </section>
</main>
</body>
</html>
```